Unique malt liquor beverage needs a logo design and bottle (6.9oz clear glass flask) label designed.

We need a logo and bottle label design for our new beverage here at Lofty Brewworks, a new company based in West Virginia. This is a differentiated product in that we use only natural ingredients and deliver it in a novel 6.9oz glass flask. Our new beverage is a naturally flavored malt liquor drink that we call "Glimmer". Our proposed tag line will be "Made to Glim" or "Cold Sip. Bold Glim". We want a logo and bottle label design that differentiates us even further.

Target Market(s)

See images I uploaded to see our two competitors...we need to be better than this but it gives you idea of the spirit of this beverage class.

Industry/Entity Type

Alcohol beverage

Requirements
Must have
• Label needs to include “14% alc/vol 6.9 oz” Both of these elements can be small and at bottom of front face of label. Also must look great on clear glass flask.
Should not have
• Do not put "malt liquor" on label. Under "Glimmer" name it will need to state "Alcoholic Beverage"

```html
<!DOCTYPE html>
<html lang="en">
<head>
<meta charset="utf-8">
<title>Glimmer — Bottle Label</title>
<link rel="stylesheet" href="https://fonts.googleapis.com/css2?family=Bodoni+Moda:opsz,wght@6..96,400;6..96,500&family=Playfair+Display:ital,wght@0,400;1,400&family=Great+Vibes&family=Oswald:wght@400&family=Josefin+Sans:wght@600&display=swap">
<style>
  :root {
    --bg: #f1ede7;
    --label-wine: #5c0013;
    --label-wine-deep: #4a000f;
    --gold: #e3a95e;
    --gold-light: #ecc592;
    --gold-shadow: #1c0004;
    --crimson: #c8102e;
    --cream: #f2e6e2;
    --ornament: rgba(255, 220, 210, 0.05);
    --flourish: rgba(255, 220, 210, 0.12);
  }
  * { margin: 0; padding: 0; box-sizing: border-box; }
  html, body { width: 1200px; height: 1200px; overflow: hidden; }
  body {
    background: var(--bg);
    display: flex; align-items: center; justify-content: center;
  }
  .label {
    position: relative;
    width: 700px; height: 1090px;
    background: linear-gradient(132deg,
      var(--label-wine) 0 43%,
      var(--label-wine-deep) 43% 71%,
      var(--label-wine) 71% 100%);
    overflow: hidden;
  }
  .centered { position: absolute; left: 0; right: 0; text-align: center; }

  .maker {
    top: 116px;
    display: flex; align-items: center; justify-content: center; gap: 16px;
    font-family: "Josefin Sans", sans-serif;
    font-weight: 600; font-size: 26px; letter-spacing: 3px;
    color: var(--gold-light);
  }
  .maker-dot {
    width: 40px; height: 40px; border-radius: 50%;
    border: 2px solid var(--gold-light);
  }

  .crest-art {
    position: absolute; left: 164px; top: 222px;
    width: 372px; height: 432px;
  }

  .product-name {
    top: 345px;
    font-family: "Bodoni Moda", serif;
    font-weight: 500; font-size: 150px; line-height: 1;
    letter-spacing: -2px;
    color: var(--gold);
    text-shadow: -5px 4px 0 var(--gold-shadow);
  }

  .tagline {
    top: 562px;
    font-family: "Playfair Display", serif;
    font-style: italic; font-size: 48px;
    color: var(--cream);
  }

  .category {
    top: 672px;
    font-family: "Playfair Display", serif;
    font-size: 60px; line-height: 0.95; letter-spacing: 3px;
    color: var(--crimson);
  }

  .flourish {
    position: absolute; left: 239px; width: 222px; height: 30px;
  }
  .flourish-top { top: 833px; }
  .flourish-bottom { top: 940px; }

  .flavor-note {
    top: 866px;
    font-family: "Great Vibes", cursive;
    font-size: 54px; line-height: 1;
    color: var(--cream);
  }

  .origin {
    top: 985px;
    font-family: "Oswald", sans-serif;
    font-size: 30px; letter-spacing: 22px;
    padding-left: 22px;
    color: var(--cream);
  }

  .volume {
    top: 1042px;
    font-family: "Oswald", sans-serif;
    font-size: 17px; letter-spacing: 4px;
    color: var(--gold-light);
  }
</style>
</head>
<body>
  <main class="label">
    <div class="centered maker">
      <span>LOFTY</span>
      <span class="maker-dot"></span>
      <span>BREWWORKS</span>
    </div>

    <svg class="crest-art" viewBox="0 0 372 432" role="img" aria-label="Faint line-drawn floral ornament behind the product name">
      <ellipse cx="186" cy="216" rx="186" ry="216" fill="var(--ornament)"/>
    </svg>

    <h1 class="centered product-name">Glimmer</h1>
    <p class="centered tagline">Made to Glim</p>
    <p class="centered category">ALCOHOLIC<br>BEVERAGE</p>

    <svg class="flourish flourish-top" viewBox="0 0 222 30" role="img" aria-label="Decorative scroll flourish">
      <rect x="0" y="12" width="222" height="6" rx="3" fill="var(--flourish)"/>
    </svg>
    <p class="centered flavor-note">Naturally Flavored</p>
    <svg class="flourish flourish-bottom" viewBox="0 0 222 30" role="img" aria-label="Decorative scroll flourish">
      <rect x="0" y="12" width="222" height="6" rx="3" fill="var(--flourish)"/>
    </svg>

    <p class="centered origin">WEST VIRGINIA</p>
    <p class="centered volume">14% ALC/VOL &nbsp;·&nbsp; 6.9 OZ</p>
  </main>
</body>
</html>
```